High-end construction company needs a business card design

We need a modern looking business card that draws people in, is memorable and looks so good people will want to sick it on their fridges.
On the first side what is needed are:
Logo
My name - Tomasz Brelwik
Title - Managing Director
Website - www.varkelt.co.uk
Email - tomasz@varkelt.co.uk
Telephone - 020 5194 6281
Mobile - 07845139072
On the back side was is needed is a list of all the services we provide:
-Kitchen Renovations
-Bathroom Renovations
-House Renovations
-Garage Conversions
-Extensions
-Loft Conversions
-Conservatories
-Carpentry
-Tiling
-Electrical
-Plumbing & Heating
-Bricklaying
-Landscaping
-Decorating
-Plastering
We would like the colours to be the same shades as on the logo with grey or black for the words.
Target Market(s)
Anyone who needs building work done
Contact Information for Business Card
This business card is for a construction company which strives to deliver excellent service and quality.
The look and feel of the card should represent this.
Requirements
Must have
- On the first side what is needed are:
Logo
My name - Tomasz Brelwik
Title - Managing Director
Website - www.varkelt.co.uk
Email - tomasz@varkelt.co.uk
Telephone - 020 5194 6281
Mobile - 07845139072
Nice to have
- Cool looking features

```html
<!DOCTYPE html>
<html lang="en">
<head>
<meta charset="utf-8">
<title>Varkelt Construction Ltd – Business Card</title>
<link href="https://fonts.googleapis.com/css2?family=Montserrat:wght@400;500;700;800&display=swap" rel="stylesheet">
<style>
  :root {
    --page-bg: #e4e4e4;
    --brand-green: #6db843;
    --brand-green-dark: #4a8b3b;
    --card-white: #f4f4f4;
    --text-dark: #222222;
    --rule-green: #5aa046;
  }
  * { box-sizing: border-box; margin: 0; padding: 0; }
  html, body {
    width: 1200px;
    height: 960px;
    overflow: hidden;
  }
  body {
    background: var(--page-bg);
    font-family: "Montserrat", sans-serif;
    position: relative;
  }
  .card {
    position: absolute;
    top: 193px;
    width: 360px;
    height: 555px;
    overflow: hidden;
  }
  .card--services {
    left: 221px;
    background: var(--brand-green);
  }
  .card--contact {
    left: 623px;
    background: var(--card-white);
  }
  .services-list {
    position: absolute;
    top: 56px;
    left: 0;
    width: 100%;
    list-style: none;
    text-align: center;
    color: var(--text-dark);
    font-size: 15px;
    font-weight: 500;
    line-height: 27.7px;
  }
  .services-art {
    position: absolute;
    left: 0;
    bottom: 0;
    width: 345px;
    height: 240px;
    background: linear-gradient(135deg, var(--brand-green) 0%, #a9d68e 45%, var(--brand-green-dark) 100%);
    clip-path: polygon(0 82%, 58% 5%, 80% 0, 100% 55%, 92% 100%, 0 100%);
  }
  .company-name {
    position: absolute;
    top: 128px;
    left: 0;
    width: 100%;
    text-align: center;
    color: var(--brand-green);
    font-weight: 800;
    line-height: 1;
  }
  .company-name__main {
    display: block;
    font-size: 46px;
    letter-spacing: 1px;
  }
  .company-name__sub {
    display: block;
    margin-top: 6px;
    font-size: 14px;
    letter-spacing: 2.4px;
  }
  .person {
    position: absolute;
    top: 247px;
    left: 0;
    width: 100%;
    text-align: center;
  }
  .person__name {
    color: var(--brand-green-dark);
    font-size: 19px;
    font-weight: 700;
    letter-spacing: 0.5px;
  }
  .person__title {
    margin-top: 2px;
    color: var(--text-dark);
    font-size: 15px;
    font-weight: 500;
  }
  .contact-list {
    position: absolute;
    top: 336px;
    left: 82px;
    width: 196px;
    list-style: none;
  }
  .contact-item {
    position: relative;
    height: 44px;
    padding-top: 12px;
    text-align: center;
    color: var(--text-dark);
    font-size: 15.5px;
    font-weight: 500;
  }
  .contact-item::before {
    content: "";
    position: absolute;
    top: 8px;
    left: 0;
    right: 0;
    height: 1px;
    background: var(--rule-green);
  }
  .contact-icon {
    position: absolute;
    top: 0;
    left: 89px;
    width: 18px;
    height: 18px;
  }
</style>
</head>
<body>

  <section class="card card--services" aria-label="Services side">
    <ul class="services-list">
      <li>Kitchen Renovations · Extensions</li>
      <li>Bathroom Renovations · Bricklaying</li>
      <li>House Renovations · Decorating</li>
      <li>Garage Conversions · Electrical</li>
      <li>Plumbing &amp; Heating · Plastering</li>
      <li>Loft Conversions · Landscaping</li>
      <li>Conservatories · Carpentry · Tiling</li>
    </ul>
    <div class="services-art" role="img" aria-label="Illustration of an excavator arm over a house roof and city buildings"></div>
  </section>

  <section class="card card--contact" aria-label="Contact side">
    <h1 class="company-name">
      <span class="company-name__main">VARKELT</span>
      <span class="company-name__sub">CONSTRUCTION LTD</span>
    </h1>

    <div class="person">
      <p class="person__name">TOMASZ BRELWIK</p>
      <p class="person__title">Managing Director</p>
    </div>

    <ul class="contact-list">
      <li class="contact-item">
        <svg class="contact-icon" viewBox="0 0 18 18" aria-hidden="true">
          <circle cx="9" cy="9" r="9" fill="var(--brand-green-dark)"/>
          <path d="M6 4.5l1.6 2.2-1 1a6 6 0 0 0 3.7 3.7l1-1 2.2 1.6-1 1.6c-3.8-.2-7-3.4-7.3-7.3z" fill="#fff"/>
        </svg>
        020 5194 6281
      </li>
      <li class="contact-item">
        <svg class="contact-icon" viewBox="0 0 18 18" aria-hidden="true">
          <circle cx="9" cy="9" r="9" fill="var(--brand-green-dark)"/>
          <rect x="6.3" y="4" width="5.4" height="10" rx="1" fill="none" stroke="#fff" stroke-width="1.2"/>
          <circle cx="9" cy="12.3" r="0.6" fill="#fff"/>
        </svg>
        0784 513 9072
      </li>
      <li class="contact-item">
        <svg class="contact-icon" viewBox="0 0 18 18" aria-hidden="true">
          <circle cx="9" cy="9" r="9" fill="var(--brand-green-dark)"/>
          <rect x="4.5" y="5.8" width="9" height="6.4" fill="none" stroke="#fff" stroke-width="1.1"/>
          <path d="M4.5 5.8L9 9.4l4.5-3.6" fill="none" stroke="#fff" stroke-width="1.1"/>
        </svg>
        tomasz@varkelt.co.uk
      </li>
      <li class="contact-item">
        <svg class="contact-icon" viewBox="0 0 18 18" aria-hidden="true">
          <circle cx="9" cy="9" r="9" fill="var(--brand-green-dark)"/>
          <g fill="none" stroke="#fff" stroke-width="1">
            <circle cx="9" cy="9" r="5"/>
            <ellipse cx="9" cy="9" rx="2.2" ry="5"/>
            <path d="M4 9h10M5 6.4h8M5 11.6h8"/>
          </g>
        </svg>
        www.varkelt.co.uk
      </li>
    </ul>
  </section>

</body>
</html>
```